App Design - Career Prep Pal

We require an App Design for our new App called 'Hiring Helper'. This app is essentially an assistant to help Users prepare for job interviews, to help them get hired. <br/><br/>Users who download the App can view common Questions and Answers, save their favourite responses and also view common Interview Tips. <br/><br/>The vision for our App is for Users who are preparing for an interview (1 week before, 1 day before, even 1 hour before), are able to download, view and educate themselves on common questions and responses, and then be confident to land the job. <br/><br/>Our team has developed wireframes to help highlight what each screen should do and include. Please see attached document, which also highlights key requirements for the experience. Feel free to add/remove/edit what you see on these wireframes. Our preference is that you use Adobe XD please.<br/><br/>In terms of design guidelines, we want the experience to be simple, intuitive and 'memorable' to help Users to remember the questions/responses when they are in the interview. <br/><br/>The final design should communicate 'neat and clean professionalism'; we like the design of: jobvista net au<br/><br/>Thank you for reading! Good luck !

Target Market(s)

Professional job seekers

Font styles to use
Sans Serif

Colors

Designer to choose colors to be used in the design.

Requirements
Must have
• Please see my PixelGuild_UX file that I have uploaded
Nice to have
• Could you also please include some ideas on how we can incorporate Advertising into the app screens

```html
<!DOCTYPE html>
<html lang="en">
<head>
<meta charset="utf-8">
<title>Hiring Helper – App Screens</title>
<link href="https://fonts.googleapis.com/css2?family=Fira+Sans:wght@400;500;600;700&display=swap" rel="stylesheet">
<style>
  :root {
    --stage: #12356e;
    --screen-top: #0c78c2;
    --screen-bottom: #6aafdc;
    --card: #ffffff;
    --ink: #1b2633;
    --icon-blue: #1c9fe0;
    --green: #7cb94b;
    --navy: #143a7a;
    --white: #ffffff;
    --art-green: rgba(124,185,75,0.55);
    --art-indigo: rgba(70,100,190,0.45);
    --art-light: rgba(255,255,255,0.22);
  }
  * { box-sizing: border-box; margin: 0; padding: 0; }
  html, body { width: 1200px; height: 661px; overflow: hidden; }
  body {
    background: var(--stage);
    font-family: "Fira Sans", sans-serif;
    color: var(--ink);
    position: relative;
  }
  a { text-decoration: none; color: inherit; }

  .screen {
    position: absolute;
    overflow: hidden;
    background: linear-gradient(180deg, var(--screen-top) 0%, var(--screen-bottom) 100%);
  }
  .screen--menu { left: 87px; top: 115px; width: 212px; height: 460px; }
  .screen--welcome { left: 358px; top: 96px; width: 234px; height: 503px; border-radius: 26px; }
  .screen--categories { left: 646px; top: 101px; width: 212px; height: 460px; }
  .screen--questions { left: 900px; top: 101px; width: 212px; height: 460px; }

  .brand { position: absolute; left: 0; right: 0; text-align: center; color: var(--white); font-weight: 600; z-index: 2; }
  .brand-mark { display: block; margin: 0 auto; background: var(--white); border-radius: 3px; }
  .screen--menu .brand { top: 19px; font-size: 17px; }
  .screen--menu .brand-mark { width: 38px; height: 36px; margin-bottom: 11px; }
  .screen--welcome .brand { top: 45px; font-size: 20.5px; }
  .screen--welcome .brand-mark { width: 50px; height: 50px; margin-bottom: 11px; }
  .header-brand { top: 10px; font-size: 9px; }
  .header-brand .brand-mark { width: 21px; height: 20px; margin-bottom: 7px; }

  /* Illustration area: soft wash in the artwork's greens and indigos */
  .art {
    position: absolute; left: 0; right: 0; bottom: 0;
    background:
      radial-gradient(ellipse 38% 26% at 36% 42%, var(--art-green) 0%, rgba(124,185,75,0) 100%),
      radial-gradient(ellipse 42% 28% at 60% 62%, var(--art-indigo) 0%, rgba(70,100,190,0) 100%),
      radial-gradient(ellipse 70% 40% at 50% 30%, var(--art-light) 0%, rgba(255,255,255,0) 100%);
  }
  .screen--menu .art { top: 300px; }
  .screen--welcome .art { top: 300px; }
  .screen--categories .art { top: 300px; opacity: .45; }
  .screen--questions .art { top: 300px; opacity: .3; }

  .menu-card {
    position: absolute; left: 13px; width: 186px; height: 59px; z-index: 2;
    background: var(--card); display: flex; align-items: center; padding: 0 13px;
  }
  .menu-card__icon {
    width: 33px; height: 33px; border-radius: 50%; background: var(--icon-blue);
    display: flex; align-items: center; justify-content: center; flex-shrink: 0;
  }
  .menu-card__label { margin-left: 24px; font-size: 10.2px; font-weight: 600; letter-spacing: .3px; line-height: 13.5px; flex: 1; }
  .menu-card__chevron { width: 7px; height: 10px; }

  .tagline {
    position: absolute; top: 236px; left: 0; right: 0; text-align: center;
    color: var(--white); font-size: 13.5px; line-height: 20px;
  }
  .btn {
    position: absolute; background: var(--green); color: var(--white); z-index: 2;
    font-weight: 600; text-align: center; box-shadow: 0 2px 4px rgba(0,0,0,.15);
  }
  .btn--start { left: 65px; top: 238px; width: 106px; height: 31px; line-height: 31px; font-size: 11.5px; letter-spacing: .2px; }
  .btn--all { left: 64px; top: 346px; width: 85px; height: 26px; line-height: 26px; font-size: 9px; }
  .screen--welcome .tagline { top: 141px; }

  .back { position: absolute; left: 12px; top: 20px; display: flex; align-items: center; gap: 6px; color: var(--white); font-size: 10px; font-weight: 500; z-index: 2; }
  .page-title { position: absolute; left: 0; right: 0; text-align: center; color: var(--white); font-size: 13.5px; font-weight: 600; line-height: 19px; letter-spacing: .3px; z-index: 2; }
  .screen--categories .page-title { top: 84px; }
  .screen--questions .page-title { top: 61px; }
  .page-sub { position: absolute; top: 127px; left: 0; right: 0; text-align: center; color: var(--white); font-size: 10px; z-index: 2; }

  .category {
    position: absolute; width: 89px; height: 81px; background: var(--card); z-index: 2;
    display: flex; flex-direction: column; align-items: center; padding-top: 12px;
  }
  .category__icon {
    width: 39px; height: 39px; border-radius: 50%; background: var(--icon-blue);
    display: flex; align-items: center; justify-content: center;
  }
  .category__label { margin-top: 12px; font-size: 9.5px; font-weight: 600; letter-spacing: .3px; }

  .tag {
    position: absolute; left: 60px; top: 107px; width: 92px; height: 26px; line-height: 26px; z-index: 2;
    background: var(--navy); color: var(--white); text-align: center; font-size: 10px; font-weight: 600; letter-spacing: .3px;
  }
  .question {
    position: absolute; left: 10px; width: 192px; background: var(--card); z-index: 2;
    display: flex; align-items: flex-start; padding: 8px 8px 0 9px;
  }
  .question__num {
    width: 14px; height: 14px; border-radius: 50%; background: var(--icon-blue); color: var(--white);
    font-size: 8.5px; font-weight: 600; text-align: center; line-height: 14px; flex-shrink: 0; margin-top: 3px;
  }
  .question__text { margin-left: 8px; font-size: 8.8px; line-height: 12.4px; font-weight: 400; }
</style>
</head>
<body>

  <!-- Main menu -->
  <section class="screen screen--menu">
    <div class="brand"><span class="brand-mark"></span>Hiring Helper</div>

    <a class="menu-card" style="top:96px">
      <span class="menu-card__icon">
        <svg width="18" height="15" viewBox="0 0 18 15"><path d="M2 1h9a1.5 1.5 0 0 1 1.5 1.5v5A1.5 1.5 0 0 1 11 9H6l-3 3V9H2A1.5 1.5 0 0 1 .5 7.5v-5A1.5 1.5 0 0 1 2 1z" fill="#fff"/><path d="M14 5h2a1.5 1.5 0 0 1 1.5 1.5v4A1.5 1.5 0 0 1 16 12h-.5v2.5L13 12H9" fill="none" stroke="#fff" stroke-width="1.2"/></svg>
      </span>
      <span class="menu-card__label">VIEW QUESTIONS<br>AND RESPONSES</span>
      <svg class="menu-card__chevron" viewBox="0 0 7 10"><path d="M1 1l4 4-4 4" fill="none" stroke="#1b2633" stroke-width="1.4"/></svg>
    </a>

    <a class="menu-card" style="top:164px">
      <span class="menu-card__icon">
        <svg width="13" height="16" viewBox="0 0 13 16"><path d="M1 1h7l4 4v10H1z" fill="#fff"/><path d="M3.5 8h6M3.5 10.5h6M3.5 13h4" stroke="#1c9fe0" stroke-width="1"/></svg>
      </span>
      <span class="menu-card__label">MY QUESTION<br>PORTFOLIO</span>
      <svg class="menu-card__chevron" viewBox="0 0 7 10"><path d="M1 1l4 4-4 4" fill="none" stroke="#1b2633" stroke-width="1.4"/></svg>
    </a>

    <a class="menu-card" style="top:232px">
      <span class="menu-card__icon">
        <svg width="12" height="17" viewBox="0 0 12 17"><path d="M6 1a5 5 0 0 0-3 9v2.5h6V10a5 5 0 0 0-3-9z" fill="#fff"/><rect x="3.5" y="13.5" width="5" height="2" rx="1" fill="#fff"/></svg>
      </span>
      <span class="menu-card__label">INTERVIEW TIPS</span>
      <svg class="menu-card__chevron" viewBox="0 0 7 10"><path d="M1 1l4 4-4 4" fill="none" stroke="#1b2633" stroke-width="1.4"/></svg>
    </a>

    <div class="art" role="img" aria-label="Illustration of people with phones sitting around large speech bubbles in a park"></div>
  </section>

  <!-- Welcome -->
  <section class="screen screen--welcome">
    <div class="brand"><span class="brand-mark"></span>Hiring Helper</div>
    <p class="tagline">Your guide to the most<br>common interview questions,<br>and the best responses to<br>help you get hired.</p>
    <a class="btn btn--start">GET STARTED</a>
    <div class="art" role="img" aria-label="Illustration of people with phones sitting around large speech bubbles in a park"></div>
  </section>

  <!-- Categories -->
  <section class="screen screen--categories">
    <div class="art" role="img" aria-label="Faded illustration of people around speech bubbles"></div>
    <div class="back">
      <svg width="11" height="10" viewBox="0 0 11 10"><path d="M5 1L1 5l4 4M1 5h10" fill="none" stroke="#fff" stroke-width="2"/></svg>Back
    </div>
    <div class="brand header-brand"><span class="brand-mark"></span>Hiring Helper</div>
    <h2 class="page-title">VIEW QUESTIONS &amp;<br>RESPONSES</h2>
    <p class="page-sub">Select your Question category</p>

    <div class="category" style="left:13px;top:159px">
      <span class="category__icon">
        <svg width="24" height="20" viewBox="0 0 24 20" fill="none" stroke="#fff" stroke-width="1.4" stroke-linejoin="round"><path d="M2 2h11v7H7l-3 3V9H2z"/><path d="M15 6h7v7h-2v3l-3-3h-6v-2"/><path d="M5 5h5M5 7h3"/></svg>
      </span>
      <span class="category__label">BEHAVIORAL</span>
    </div>
    <div class="category" style="left:109px;top:159px">
      <span class="category__icon">
        <svg width="18" height="22" viewBox="0 0 18 22" fill="none" stroke="#fff" stroke-width="1.4" stroke-linecap="round"><path d="M9 2a6.5 6.5 0 0 0-3.8 11.8V16h7.6v-2.2A6.5 6.5 0 0 0 9 2z"/><path d="M6.5 18.5h5M7.5 20.5h3"/><path d="M9 6l-2 4h4l-2 4"/></svg>
      </span>
      <span class="category__label">SITUATIONAL</span>
    </div>
    <div class="category" style="left:13px;top:247px">
      <span class="category__icon">
        <svg width="24" height="18" viewBox="0 0 24 18" fill="none" stroke="#fff" stroke-width="1.6" stroke-linecap="round" stroke-linejoin="round"><path d="M2 16l6-6 4 3 9-9"/><path d="M15 4h6v6"/></svg>
      </span>
      <span class="category__label">MOTIVATIONAL</span>
    </div>
    <div class="category" style="left:109px;top:247px">
      <span class="category__icon">
        <svg width="22" height="22" viewBox="0 0 22 22" fill="none" stroke="#fff" stroke-width="1.4"><path d="M11 2.5l1.6 2.3 2.7-.8.5 2.8 2.6 1-1 2.6 1.6 2.3-2.4 1.5.1 2.8-2.8.3-1.1 2.6L11 18.4l-2.4 1.5-1.1-2.6-2.8-.3.1-2.8-2.4-1.5 1.6-2.3-1-2.6 2.6-1 .5-2.8 2.7.8z" stroke-linejoin="round"/><circle cx="11" cy="11" r="3.2"/></svg>
      </span>
      <span class="category__label">TECHNICAL</span>
    </div>

    <a class="btn btn--all">VIEW ALL</a>
  </section>

  <!-- Question list -->
  <section class="screen screen--questions">
    <div class="art" role="img" aria-label="Faded illustration of people around speech bubbles"></div>
    <div class="back">
      <svg width="11" height="10" viewBox="0 0 11 10"><path d="M5 1L1 5l4 4M1 5h10" fill="none" stroke="#fff" stroke-width="2"/></svg>Back
    </div>
    <div class="brand header-brand"><span class="brand-mark"></span>Hiring Helper</div>
    <h2 class="page-title">VIEW QUESTIONS &amp;<br>RESPONSES</h2>
    <div class="tag">BEHAVIORAL</div>

    <div class="question" style="top:148px;height:65px"><span class="question__num">1</span><p class="question__text">Give me an example of a new idea or initiative you have suggested to your manager. How did you implement this idea?</p></div>
    <div class="question" style="top:222px;height:65px"><span class="question__num">2</span><p class="question__text">Give me an example of a time when you made a mistake or didn't deliver on expectations, what happened? What did you learn?</p></div>
    <div class="question" style="top:295px;height:42px"><span class="question__num">3</span><p class="question__text">How would your colleagues describe you in three words?</p></div>
    <div class="question" style="top:346px;height:42px"><span class="question__num">4</span><p class="question__text">What parts of your current role frustrate you</p></div>
    <div class="question" style="top:397px;height:42px"><span class="question__num">5</span><p class="question__text">What steps would you take to make an important decision on the job?</p></div>
  </section>

</body>
</html>
```